Business Card Design

We like to use greens as you will see in our logo (but not TOO much green). We are a Dental Clinic in a somewhat eccentric community. We do not like the dated sharp designs which we see many dentists use. We're looking for something bright and fresh while still maintaining the integrity of the profession. Elegance is not necessarily what we are going for... we need for the design to be "mature" but also up-lifting.

See our logo.
Updates

Project Deadline Extended
Reason: We have 5 designs which we like. But we'd like to see a few more before committing to a design.

Project Deadline Extended
Reason: We are awaiting revisions to this project. We are still welcoming designs while we wait to see if designers are able to provide to us the revisions we require in order to proceed with a selection.

Target Market(s)

Younger families - ages late 20's to early 40's

Industry/Entity Type

Business

Contact Information for Business Card

Corwel T. Banfry DDS 2730 W. Halvert Rd. Ste. 7 Royal Oak, MI 48391 (248)555-0174 FX (248)555-0189 info@BrightwellDentalCareMi.com BrigthwellDentalCareMi.com on the back of the card we need an appointment reminder (For____ Date___ Time____) with "If you are unable to keep your appointment, kindly give 48 hours notice" at the bottom. No use of teeth in the design. DOUBLE SIDED DESIGN

Requirements
Should not have
• The use of pictures of teeth

```html
<!DOCTYPE html>
<html lang="en">
<head>
<meta charset="utf-8">
<title>Brightwell Dental Care – Business Card</title>
<link rel="stylesheet" href="https://fonts.googleapis.com/css2?family=Arimo:wght@400;700&family=Cinzel:wght@500&family=Open+Sans:ital,wght@0,400;0,600;1,400&display=swap">
<style>
  :root {
    --backdrop: #e9e6e1;
    --card: #ffffff;
    --brand-green: #1f6b35;
    --accent-green: #8cc63f;
    --ink: #222222;
    --ink-soft: #444444;
    --ink-muted: #555555;
    --rule: #666666;
  }
  * { margin: 0; padding: 0; box-sizing: border-box; }
  html, body {
    width: 1200px; height: 1159px; overflow: hidden;
    background: var(--backdrop);
  }
  .card {
    position: absolute;
    width: 911px; height: 519px;
    background: var(--card);
    box-shadow: 0 2px 8px rgba(0,0,0,.18);
  }
  .card--front { left: 26px; top: 51px; }
  .card--back { left: 238px; top: 593px; }

  /* Front */
  .brand { position: absolute; left: 46px; top: 120px; font-family: "Cinzel", serif; font-weight: 500; color: var(--brand-green); }
  .brand__name { font-size: 62px; line-height: 1; letter-spacing: 1px; }
  .brand__line { font-size: 41px; line-height: 1; margin-top: 10px; letter-spacing: 2px; }
  .person { position: absolute; left: 52px; top: 310px; font-family: "Arimo", sans-serif; }
  .person__name { font-size: 32px; font-weight: 700; color: var(--brand-green); }
  .person__title { font-size: 20px; font-weight: 700; color: var(--ink); margin-top: 14px; }
  .website { position: absolute; left: 44px; top: 474px; font-family: "Arimo", sans-serif; font-size: 22px; color: var(--ink); }
  .website__domain { color: var(--brand-green); }
  .divider { position: absolute; left: 455px; top: 316px; width: 2px; height: 203px; background: var(--brand-green); }
  .contacts { position: absolute; left: 467px; top: 312px; list-style: none; font-family: "Arimo", sans-serif; font-size: 23px; color: var(--ink-soft); }
  .contacts li { display: flex; align-items: flex-start; gap: 9px; height: 42px; }
  .contacts li.contacts__address { line-height: 28px; margin-top: 6px; }
  .contacts svg { width: 20px; height: 20px; flex: none; margin-top: 4px; fill: var(--ink-soft); }

  /* Back */
  .appt-title { position: absolute; left: 0; right: 0; top: 88px; text-align: center; font-family: "Cinzel", serif; font-weight: 500; font-size: 33px; color: var(--brand-green); letter-spacing: 1px; }
  .label { position: absolute; font-family: "Open Sans", sans-serif; font-size: 26px; color: var(--ink-soft); line-height: 1; }
  .dots { position: absolute; border-bottom: 2px dotted var(--ink-muted); height: 0; }
  .slot { position: absolute; border: 2px solid var(--ink-muted); border-radius: 4px; }
  .day { position: absolute; font-family: "Open Sans", sans-serif; font-weight: 600; font-size: 25px; color: var(--ink-muted); line-height: 1; }
  .notice { position: absolute; left: 0; right: 0; top: 450px; text-align: center; font-family: "Open Sans", sans-serif; font-style: italic; font-size: 25px; color: var(--ink); }
</style>
</head>
<body>

<section class="card card--front" aria-label="Card front">
  <div class="brand">
    <div class="brand__name">Brightwell</div>
    <div class="brand__line">DENTAL CARE</div>
  </div>
  <div class="person">
    <div class="person__name">Corwel T. Banfry</div>
    <div class="person__title">DDS</div>
  </div>
  <div class="website">www.<span class="website__domain">BrigthwellDentalCare</span>Mi.com</div>
  <div class="divider"></div>
  <ul class="contacts">
    <li>
      <svg viewBox="0 0 24 24" aria-hidden="true"><path d="M6.6 10.8a15 15 0 0 0 6.6 6.6l2.2-2.2c.3-.3.7-.4 1-.2 1.1.4 2.3.6 3.6.6.6 0 1 .4 1 1V20c0 .6-.4 1-1 1A17 17 0 0 1 3 4c0-.6.4-1 1-1h3.5c.6 0 1 .4 1 1 0 1.2.2 2.4.6 3.6.1.3 0 .7-.2 1z"/></svg>
      <span>(248) 555-0174</span>
    </li>
    <li>
      <svg viewBox="0 0 24 24" aria-hidden="true"><path d="M6 2h9l3 3v4H6zM4 10h16a2 2 0 0 1 2 2v6h-4v4H6v-4H2v-6a2 2 0 0 1 2-2zm4 7v3h8v-3z"/></svg>
      <span>(248) 555-0189</span>
    </li>
    <li>
      <svg viewBox="0 0 24 24" aria-hidden="true"><path d="M2 6h20v12H2zm2 2v.4l8 5 8-5V8zm0 2.8V16h16v-5.2l-8 5z"/></svg>
      <span>info@BrightwellDentalCareMi.com</span>
    </li>
    <li class="contacts__address">
      <svg viewBox="0 0 24 24" aria-hidden="true"><path d="M12 2a7 7 0 0 0-7 7c0 5 7 13 7 13s7-8 7-13a7 7 0 0 0-7-7zm0 9.5A2.5 2.5 0 1 1 12 6.5a2.5 2.5 0 0 1 0 5z"/></svg>
      <span>2730 W. Halvert Rd.<br>Ste. 7 Royal Oak, MI 48391</span>
    </li>
  </ul>
</section>

<section class="card card--back" aria-label="Card back">
  <h2 class="appt-title">YOUR APPOINTMENT</h2>

  <span class="label" style="left:71px; top:156px;">Name :</span>
  <div class="dots" style="left:172px; width:661px; top:178px;"></div>

  <span class="label" style="left:71px; top:221px;">Date :</span>
  <div class="dots" style="left:172px; width:228px; top:243px;"></div>
  <span class="label" style="left:408px; top:221px;">Time :</span>
  <div class="dots" style="left:489px; width:242px; top:243px;"></div>
  <span class="label" style="left:742px; top:221px;">am / pm</span>

  <span class="label" style="left:71px; top:285px;">Next Appointment</span>
  <div class="slot" style="left:322px; top:280px; width:164px; height:35px;"></div>
  <div class="slot" style="left:500px; top:280px; width:164px; height:35px;"></div>
  <div class="slot" style="left:674px; top:280px; width:164px; height:35px;"></div>

  <span class="day" style="left:68px; top:374px;">MON</span>
  <div class="slot" style="left:143px; top:370px; width:55px; height:33px;"></div>
  <span class="day" style="left:213px; top:374px;">TUE</span>
  <div class="slot" style="left:271px; top:370px; width:55px; height:33px;"></div>
  <span class="day" style="left:338px; top:374px;">WED</span>
  <div class="slot" style="left:411px; top:370px; width:55px; height:33px;"></div>
  <span class="day" style="left:476px; top:374px;">THU</span>
  <div class="slot" style="left:546px; top:370px; width:55px; height:33px;"></div>
  <span class="day" style="left:610px; top:374px;">FRI</span>
  <div class="slot" style="left:661px; top:370px; width:55px; height:33px;"></div>
  <span class="day" style="left:727px; top:374px;">SAT</span>
  <div class="slot" style="left:786px; top:370px; width:55px; height:33px;"></div>

  <p class="notice">If you are unable to keep your appointment, kindly give 48 hours notice</p>
</section>

</body>
</html>
```